Podiatry clinic requires a modern revamp and editing of existing website.

I would like a fresh new look and updated information for my current business website. An easy to navigate site with prominent address and phone number for call to action. We are a podiatry clinic that focuses on general and sports podiatry.
I would like 4 pages; including Home page, About Us, Services & Contact.
www.brambleridgepodiatry.net

Target Market(s)

Active working professionals.

Industry/Entity Type

Medical

Coding

Coded - Design and coding required

Number of Pages Required

4 page

Font styles to use
Sans Serif

Colors
6b449b

Requirements
Must have
• A modern look with logo and active images; clean and uncluttered. Visible phone number and address for call to action.
• 4 pages - Home, About Us, Services, Contact.
• Home page - update address & service logos.
• About Us - update of personal information.
• Services - Revamp of existing page.
• Contact page to include Google map, email & phone number.
Nice to have
• Ability to add content easily; eg. a blog or adding video onto Home page.
• Link to Facebook page.

```html
<!DOCTYPE html>
<html lang="en">
<head>
<meta charset="utf-8">
<title>Bramble Ridge Podiatry</title>
<link href="https://fonts.googleapis.com/css2?family=Raleway:wght@400;500;600;700;800&family=Great+Vibes&display=swap" rel="stylesheet">
<style>
:root{
  --purple:#6b449b;
  --purple-deep:#3b2463;
  --purple-soft:#a58fd0;
  --ink:#1d1d1d;
  --grey:#8a8a8a;
  --band:#f4f4f4;
  --footer:#333333;
  --footer-bottom:#1c1c1c;
  --white:#ffffff;
}
*{margin:0;padding:0;box-sizing:border-box}
html,body{width:670px;height:1200px;overflow:hidden;background:var(--white)}
body{font-family:"Raleway",Arial,sans-serif;color:var(--ink);position:relative}
.abs{position:absolute}

/* header */
.site-header{position:absolute;left:0;top:0;width:670px;height:47px;background:var(--white);border-bottom:1.5px solid var(--purple);z-index:3}
.brand{position:absolute;left:30px;top:-30px;width:102px;height:108px;border-radius:0 0 51px 51px;background:var(--white);border:1.5px solid var(--purple);border-top:none;z-index:4;display:flex;align-items:center;justify-content:center;gap:5px;padding-top:34px}
.brand-dot{width:9px;height:9px;border-radius:50%;background:var(--purple)}
.brand-name{font-weight:700;font-size:11px;line-height:12px;color:var(--purple)}
.main-nav{position:absolute;top:17px;left:187px;display:flex;gap:0;font-size:9.5px;font-weight:500;letter-spacing:.2px}
.main-nav a{color:var(--ink);text-decoration:none;position:absolute;white-space:nowrap}
.main-nav a.active{color:var(--purple);font-weight:700}
.call{position:absolute;left:507px;top:10px}
.call-label{position:absolute;left:28px;top:0;font-size:7.5px;color:#555;white-space:nowrap}
.call-number{position:absolute;left:28px;top:9px;font-size:14px;font-weight:700;color:var(--purple);white-space:nowrap}

/* hero */
.hero{position:absolute;left:0;top:47px;width:670px;height:331px;background:linear-gradient(90deg,#eeeeee,#f2f2f2)}
.hero-photo{position:absolute;right:0;top:0;width:300px;height:331px;background:linear-gradient(135deg,#e9e9e9 0%,#d9d3cf 45%,#b9b2ad 75%,#8f8b86 100%)}
.hero-title{position:absolute;left:44px;top:95px;font-size:29px;line-height:35px}
.hero-title .l1{display:block;color:var(--purple);font-weight:800}
.hero-title .l2{display:block;margin-left:71px;font-weight:500;color:#111}
.hero-sub{position:absolute;left:44px;top:172px;font-size:17px;font-weight:500}
.btn{position:absolute;top:215px;height:29px;border-radius:3px;color:var(--white);font-size:9.5px;font-weight:500;display:flex;align-items:center;justify-content:center;gap:6px}
.btn-video{left:43px;width:105px;background:var(--purple-deep)}
.btn-book{left:159px;width:140px;background:var(--purple)}

/* partners */
.partners{position:absolute;left:0;top:378px;width:670px;height:71px;background:var(--white);box-shadow:0 2px 4px rgba(0,0,0,.08)}
.badge{position:absolute;top:20px;height:30px;border-radius:4px}

/* welcome */
.welcome{position:absolute;left:0;top:449px;width:670px;height:232px;background:var(--white)}
.video{position:absolute;left:43px;top:29px;width:291px;height:174px;background:#6e5a8e}
.video-art{position:absolute;left:0;top:0;width:291px;height:157px;background:linear-gradient(135deg,#6f5b91,#64528a)}
.video-bar{position:absolute;left:0;bottom:0;width:291px;height:17px;background:#111;color:#ddd;font-size:6px}
.welcome-copy{position:absolute;left:354px;top:32px;width:274px;text-align:center}
.welcome-script{font-family:"Great Vibes",cursive;font-size:22px;line-height:22px}
.welcome-title{font-size:24px;color:var(--purple);font-weight:500;line-height:28px;margin-top:-2px}
.welcome-text{font-size:7.3px;line-height:12.8px;color:#555;margin-top:10px}

/* services */
.services{position:absolute;left:0;top:681px;width:670px;height:316px;background:var(--band)}
.services-title{position:absolute;left:0;width:670px;top:27px;text-align:center;font-size:24px;font-weight:500}
.svc{position:absolute;width:190px}
.svc h3{font-size:11.5px;font-weight:500;letter-spacing:.3px;color:#222}
.svc p{font-size:7.3px;line-height:12.8px;color:var(--grey);margin-top:6px}
.svc.left{text-align:right}
.svc-icon{position:absolute;width:26px;height:28px;background:#a9a9a9;border-radius:5px}
.svc-line{position:absolute;width:1px;background:#c9c9c9}
.foot-art{position:absolute;left:298px;top:95px;width:74px;height:143px;background:var(--purple);border-radius:40px 40px 30px 30px}

/* footer */
.site-footer{position:absolute;left:0;top:997px;width:670px;height:173px;background:var(--footer);color:#aaa}
.fcol{position:absolute;top:16px}
.fcol h4{font-size:15px;font-weight:500;color:var(--purple-soft);margin-bottom:14px}
.fcol ul{list-style:none}
.fcol li{font-size:7.5px;height:21px;line-height:20px;border-bottom:1px solid #4e4e4e;color:#7d7d7d}
.fcol li:first-child{color:var(--white)}
.fcol li:last-child{border-bottom:none}
.footer-divider{position:absolute;left:453px;top:16px;width:1px;height:150px;background:#555}
.contact-row{position:absolute;left:477px;font-size:7.5px;line-height:11px;color:#ddd}
.contact-row svg{position:absolute;left:0;top:0}
.contact-row span{position:absolute;left:18px;white-space:nowrap}
.social{position:absolute;top:129px;width:23px;height:23px;border-radius:50%}
.bottom-bar{position:absolute;left:0;top:1170px;width:670px;height:30px;background:var(--footer-bottom);color:var(--white);font-size:7.5px;font-weight:700;text-align:center;line-height:30px}
.bottom-bar b{color:var(--purple-soft)}
</style>
</head>
<body>

<header class="site-header">
  <nav class="main-nav">
    <a class="active" style="left:0">HOME</a>
    <a style="left:55px">ABOUT US</a>
    <a style="left:129px">PODIATRY SERVICES</a>
    <a style="left:250px">CONTACT</a>
  </nav>
  <div class="call">
    <svg width="22" height="22" viewBox="0 0 24 24" fill="none" stroke="#222" stroke-width="1.5"><path d="M5 3h4l2 5-2.5 1.5a11 11 0 0 0 6 6L16 13l5 2v4a2 2 0 0 1-2 2A16 16 0 0 1 3 5a2 2 0 0 1 2-2z"/><path d="M15 3a6 6 0 0 1 6 6M15 6.5a2.5 2.5 0 0 1 2.5 2.5"/></svg>
    <span class="call-label">CALL US NOW</span>
    <span class="call-number">1300 482 907</span>
  </div>
</header>
<div class="brand"><span class="brand-dot"></span><span class="brand-name">Bramble<br>Ridge<br>Podiatry</span></div>

<section class="hero">
  <div class="hero-photo" role="img" aria-label="Podiatrist stretching the leg of a patient lying on a treatment table"></div>
  <h1 class="hero-title"><span class="l1">STEP UP &amp; REACH</span><span class="l2">YOUR POTENTIAL</span></h1>
  <p class="hero-sub">Visit us at Bramble Ridge Podiatry</p>
  <a class="btn btn-video"><svg width="14" height="14" viewBox="0 0 14 14"><circle cx="7" cy="7" r="7" fill="#fff"/><path d="M5.5 4l4 3-4 3z" fill="#3b2463"/></svg>WATCH VIDEO</a>
  <a class="btn btn-book">BOOK AN APPOINTMENT</a>
</section>

<section class="partners" aria-label="Partners">
  <div class="badge" style="left:70px;width:86px;background:#f2c26b"></div>
  <div class="badge" style="left:219px;width:86px;background:#2b5d9c"></div>
  <div class="badge" style="left:352px;width:115px;background:#1f9a4b"></div>
  <div class="badge" style="left:493px;width:128px;background:#2a3566"></div>
</section>

<section class="welcome">
  <div class="video">
    <div class="video-art" role="img" aria-label="Clinic introduction video still"></div>
    <svg class="abs" style="left:122px;top:63px" width="46" height="46" viewBox="0 0 46 46"><circle cx="23" cy="23" r="21" fill="none" stroke="#fff" stroke-width="3"/><path d="M18 13l14 10-14 10z" fill="#fff"/></svg>
    <div class="video-bar">
      <svg class="abs" style="left:5px;top:5px" width="7" height="7" viewBox="0 0 7 7"><path d="M0 0l7 3.5L0 7z" fill="#fff"/></svg>
      <span class="abs" style="left:16px;top:5px">00:00</span>
      <span class="abs" style="left:37px;top:6px;width:223px;height:5px;background:#eee;border-radius:2px"></span>
      <span class="abs" style="left:243px;top:5px;left:244px">00:42</span>
      <svg class="abs" style="left:263px;top:4px" width="9" height="9" viewBox="0 0 9 9"><path d="M0 3h2l3-3v9L2 6H0z" fill="#fff"/></svg>
      <svg class="abs" style="left:279px;top:4px" width="8" height="8" viewBox="0 0 8 8" fill="none" stroke="#fff"><path d="M0 3V0h3M5 0h3v3M8 5v3H5M3 8H0V5"/></svg>
    </div>
  </div>
  <div class="welcome-copy">
    <div class="welcome-script">Welcome to</div>
    <h2 class="welcome-title">bramble ridge podiatry</h2>
    <p class="welcome-text">Bramble Ridge Podiatry is a Podiatry clinic in the heart of Melbourne CBD. We are located between Ellery &amp; Gowan Streets in the Harrow Chambers / Linden Court Complex. Our podiatrists are fully qualified health professionals who are able to diagnose, treat, manage or help to prevent all medical conditions that affect the feet and lower limb. We provide General Podiatry Treatment and some Specialised Services in relation to various foot conditions, including Sports Injuries, Orthotic Therapy and Nail Surgery.</p>
  </div>
</section>

<section class="services">
  <h2 class="services-title">Services We Provide</h2>

  <div class="svc left" style="left:38px;top:72px"><h3>DIABETIC MANAGEMENT</h3><p>Assessment of blood supply/circulation with Doppler Ultrasound; Assessment of nerve sensation via Vibration...</p></div>
  <div class="svc left" style="left:38px;top:154px"><h3>NAIL SURGERY</h3><p>Minor surgical procedure for the permanent removal of ingrown toenails under local anaesthesia.</p></div>
  <div class="svc left" style="left:38px;top:229px"><h3>BIOMECHANICAL ASSESSMENT</h3><p>We are able to help diagnose abnormal foot biomechanics that may be contributing to pain, injury or deformities in the foot and lower limb.</p></div>

  <div class="svc-icon" role="img" aria-label="Hands icon" style="left:240px;top:83px"></div>
  <div class="svc-line" style="left:254px;top:116px;height:36px"></div>
  <div class="svc-icon" role="img" aria-label="Toe and nail icon" style="left:242px;top:168px;width:34px;height:22px"></div>
  <div class="svc-line" style="left:254px;top:196px;height:36px"></div>
  <div class="svc-icon" role="img" aria-label="Foot side view icon" style="left:238px;top:244px;width:34px;height:26px"></div>

  <div class="foot-art" role="img" aria-label="Large footprint illustration"></div>

  <div class="svc-icon" role="img" aria-label="Footprints icon" style="left:400px;top:124px;width:20px;height:30px"></div>
  <div class="svc-line" style="left:410px;top:160px;height:36px"></div>
  <div class="svc-icon" role="img" aria-label="Orthotic brace icon" style="left:398px;top:202px;width:20px;height:32px"></div>

  <div class="svc" style="left:442px;top:113px;width:200px"><h3>GAIT ANALYSIS</h3><p>Treadmill analysis of the gait whilst walking or running to ascertain biomechanical problems or abnormalities...</p></div>
  <div class="svc" style="left:442px;top:188px;width:200px"><h3>ORTHOTIC THERAPY</h3><p>Orthoses, or arch supports, are designed to control the function of the foot when there is evidence of faulty biomechanics.</p></div>
</section>

<footer class="site-footer">
  <div class="fcol" style="left:44px;width:93px"><h4>Usefull links</h4><ul><li>Home</li><li>About us</li><li>Services</li><li>Contact</li></ul></div>
  <div class="fcol" style="left:155px;width:127px"><h4>Products</h4><ul><li>Softstep Heel Balm</li><li>Trailguard Anti-Chafe Stick</li><li>Fernleaf Foot Scrub &amp; Oil</li><li>Verdane Cooling Cream &amp; Spray</li><li>Clearpath Antifungal Cream</li></ul></div>
  <div class="fcol" style="left:300px;width:122px"><h4>Blog</h4><ul><li>Lorem ipsum is simply dummy</li><li>Lorem ipsum is simply dummy</li><li>Lorem ipsum is simply dummy</li><li>Lorem ipsum is simply dummy</li><li>Lorem ipsum is simply dummy</li></ul></div>
  <div class="footer-divider"></div>
  <div class="fcol" style="left:477px"><h4>Contact Information</h4></div>
  <div class="contact-row" style="top:55px">
    <svg width="12" height="15" viewBox="0 0 12 15" fill="none" stroke="#a58fd0"><path d="M6 14S1 8.5 1 5.5a5 5 0 0 1 10 0C11 8.5 6 14 6 14z"/><circle cx="6" cy="5.5" r="1.8"/></svg>
    <span style="top:0">Suite 214 / 62 Harrow Street</span><span style="top:11px">Melbourne 3000.</span>
  </div>
  <div class="contact-row" style="top:91px">
    <svg width="12" height="12" viewBox="0 0 24 24" fill="none" stroke="#a58fd0" stroke-width="2"><path d="M5 3h4l2 5-2.5 1.5a11 11 0 0 0 6 6L16 13l5 2v4a2 2 0 0 1-2 2A16 16 0 0 1 3 5a2 2 0 0 1 2-2z"/></svg>
    <span style="top:1px">1300 482 907</span>
  </div>
  <div class="contact-row" style="top:114px">
    <svg width="12" height="10" viewBox="0 0 12 10" fill="none" stroke="#a58fd0"><rect x=".5" y=".5" width="11" height="9"/><path d="M.5.5L6 5.5 11.5.5"/></svg>
    <span style="top:0">info@brambleridgepodiatry.net</span>
  </div>
  <div class="social" style="left:477px;border:1px solid var(--purple-soft)"></div>
  <div class="social" style="left:506px;background:var(--white)"></div>
  <div class="social" style="left:534px;background:var(--white)"></div>
</footer>
<div class="bottom-bar">© <b>bramble ridge podiatry</b> - 2016. All Rights Reserved.</div>

</body>
</html>
```